Research and Innovation programme/projects in WOOD based industries

1.Pramenova s.r.o. (offical registered brand name of our company)
-Managing technology development projects
-International cooperation and development European projects
Our company was founded in 2008 and started to work as a counsilary company operating in the section of european funds administrated by Czech republic. Nowadays we are specializing on projects in the sphere of science and research co-financed by EU.Since 6.6.2013 we are registered under European comission for a purpose of broad support of transnational projects.

Target Market(s)

We are primarily focused on european companies, which stand behind the latest research and innovation of sawing, planing, glulam and logging technologies based on wooden materials.

Coding

Coded - Design and coding required

Number of Pages Required

5+ page

Font styles to use
Serif

Colors
cadf82
abd037
9bcb3c
fee18a
ffcf3e
ffc214

Requirements
Must have
• The web will exist in three possible languages in czech, english and deutsch.
• First page : introduction of a company
• Second page : Area of expertise
• Third page: servicies our company provides
• Fourth page: Our partners
• Fifth page: Conditions of our servicies
• Sixth page: Succesful projects
• - we would also love if we had possibility to add videos about our successful projects
• Seventh: Our team
• We are serious company in the sphere of funds and counsilary servicies, that is why we would love to have web design as representative as possible
• Take on mind that that we are specializing on development management, try to apply that on your design
• In the section of contacts, we would love to have photos of our team,
• This is our current site: http://www.pramenova-example.eu/cz/partneri.html
• This is how our concurency sites are lookin. Take these designs as an slight inspiration.
• http://www.lumatrava-example.sk/en/
• https://www2.brenvick-example.com/global/en.html
Nice to have
• Visible logo on the front page for the visitor.
• As a inspiration we provided link for our current web design, but we dont want to copy the current style, just look at the logo and the pages that exists on current web.
• !!!!!!We also uploaded file, where we explain how our cooperation with partner works. Especially in the part 2. section of service. Take that as an ispiration too, or use that to understand, what our company do.
Should not have
• We are serious company in the sphere of funds and counsilary servicies, that is why we would love to have web design representative as possible

```html
<!DOCTYPE html>
<html lang="en">
<head>
<meta charset="utf-8">
<title>1. Pramenova s.r.o. – Research and innovation in wood based industries</title>
<link href="https://fonts.googleapis.com/css2?family=Poppins:wght@400;600;700&family=Open+Sans:wght@400;600&display=swap" rel="stylesheet">
<style>
:root{
  --green:#21862f;
  --green-light:#8dc63f;
  --lime:#abd037;
  --yellow:#ffc214;
  --yellow-soft:#ffcf3e;
  --grey:#efefef;
  --tile:#e6e6e6;
  --text:#333;
  --muted:#666;
  --dark:#1d1d1d;
  --white:#fff;
}
*{box-sizing:border-box;margin:0;padding:0}
html,body{width:1200px;height:4559px;overflow:hidden}
body{font-family:"Open Sans",Arial,sans-serif;color:var(--text);background:var(--white);position:relative}
h2{font-family:"Poppins",Arial,sans-serif;font-weight:700;color:var(--green);font-size:31px;text-align:center;letter-spacing:.2px}
.btn{display:inline-block;background:var(--green-light);color:#1b3b10;font-family:"Poppins",Arial,sans-serif;font-weight:600;font-size:12px;padding:11px 17px;text-transform:uppercase}
.section{position:absolute;left:0;width:1200px}
.diag{position:absolute;left:0;width:1200px;display:block}

/* header + hero */
.hero{top:0;height:694px;background:linear-gradient(135deg,#6b6257 0%,#8a7f6f 30%,#5d5a55 55%,#3e3c3a 100%)}
.hero-photo{position:absolute;inset:0}
.topbar{position:absolute;top:0;left:0;width:1200px;height:70px;background:linear-gradient(#000c,#0000)}
.brand{position:absolute;left:143px;top:18px;display:flex;align-items:center;gap:10px}
.brand-mark{width:46px;height:32px;background:var(--lime)}
.brand-name{font-family:"Poppins",Arial,sans-serif;font-size:17px;color:var(--lime);line-height:1}
.brand-sub{font-size:9px;color:#fff;margin-top:3px}
.nav{position:absolute;right:143px;top:36px;display:flex;gap:22px;font-family:"Poppins",Arial,sans-serif;font-size:10.5px;color:#fff}
.nav .active{color:var(--yellow)}
.langs{position:absolute;right:143px;top:17px;display:flex;gap:8px}
.langs span{width:14px;height:9px;display:block}
.hero-title{position:absolute;top:236px;left:0;width:1200px;text-align:center;font-family:"Poppins",Arial,sans-serif;font-weight:700;font-size:32px;line-height:43px;color:#fff;text-transform:uppercase}
.hero .btn{position:absolute;top:375px;left:547px}
.arrow-side{position:absolute;top:316px;width:24px;height:32px;background:#0008;display:flex;align-items:center;justify-content:center}

/* welcome */
.welcome{top:694px;height:294px;text-align:center;padding-top:74px}
.lead{font-size:12.5px;line-height:24px;width:900px;margin:18px auto 0;color:var(--text)}

/* expertise */
.expertise{top:988px;height:440px;background:var(--tile)}
.expertise-copy{position:absolute;left:143px;top:92px;width:420px}
.expertise-copy h2{text-align:left;font-size:29px}
.expertise-copy p{font-size:12.5px;line-height:24px;margin:12px 0 22px}
.expertise-photo{position:absolute;left:600px;top:0;width:600px;height:440px;background:linear-gradient(160deg,#9a9a9a,#5c5a55 55%,#8a6a48)}

/* services */
.services{top:1428px;height:595px;padding-top:74px}
.tiles{position:absolute;left:143px;top:130px;display:grid;grid-template-columns:repeat(4,218px);gap:14px}
.tile{height:184px;background:var(--tile);display:flex;flex-direction:column;align-items:center;justify-content:center;text-align:center;font-family:"Poppins",Arial,sans-serif;font-size:14px;line-height:22px;color:#444}
.tile svg{margin-bottom:16px}
.tile.more{font-weight:700;font-size:22px;color:#bdbdbd}

/* partners */
.partners{top:2023px;height:317px;background:var(--grey);text-align:center;padding-top:100px}
.partner-row{display:flex;justify-content:center;align-items:center;gap:30px;margin-top:24px}
.badge{background:#dcdcdc}

/* conditions */
.conditions{top:2340px;height:360px;text-align:center;padding-top:86px}
.conditions .btn{margin-top:20px}

/* projects */
.projects{top:2700px;height:513px;background:var(--grey);padding-top:108px}
.cards{position:absolute;left:143px;top:167px;display:flex;gap:24px}
.card{width:288px}
.card-img{height:191px;position:relative;display:flex;align-items:center;justify-content:center}
.card p{font-family:"Poppins",Arial,sans-serif;font-size:12.5px;line-height:22px;color:var(--green-light);margin-top:6px}
.chev{position:absolute;top:248px}

/* team */
.team{top:3213px;height:522px;padding-top:72px}
.people{position:absolute;left:143px;top:132px;display:flex;gap:14px}
.person{width:218px;background:var(--tile);text-align:center}
.person-img{height:241px}
.person h3{font-weight:400;font-size:15px;color:#444;margin-top:12px}
.person span{display:block;font-size:10.5px;color:var(--muted);margin:5px 0 14px}

/* contact */
.contact{top:3735px;height:780px;background:var(--grey);text-align:center;padding-top:120px}
.contact p{font-size:15px;line-height:28px;color:#222}
.map{position:absolute;left:143px;top:235px;width:912px;height:317px;border:4px solid #fff;background:linear-gradient(135deg,#dbe6cf,#eef0e8 45%,#d6e3c7)}

/* footer */
.footer{top:4407px;height:152px;background:var(--dark)}
.footer-links{position:absolute;left:143px;top:75px;font-size:10px;color:#bbb}
.footer-links b{font-weight:400;margin:0 7px;color:#777}
.copy{position:absolute;left:143px;top:102px;font-size:10px;color:#999}
.social{position:absolute;left:1002px;top:85px;display:flex;gap:12px}
.social span{width:12px;height:12px;border-radius:50%;background:#aaa}
.mark{position:absolute;right:12px;bottom:8px;font-size:9px;color:#777}
</style>
</head>
<body>

<section class="section hero">
  <div class="hero-photo" role="img" aria-label="Worker carrying a wooden door panel through a woodworking production hall"></div>
  <div class="topbar"></div>
  <div class="brand">
    <div class="brand-mark"></div>
    <div><div class="brand-name">1. Pramenova s.r.o.</div><div class="brand-sub">Beratungsfirma</div></div>
  </div>
  <div class="langs">
    <span style="background:#1f3d7a;box-shadow:inset 0 4px 0 -3px #c00"></span>
    <span style="background:linear-gradient(#000 33%,#d00 33% 66%,#fc0 66%)"></span>
    <span style="background:linear-gradient(#fff 50%,#d7141a 50%);box-shadow:inset 6px 0 0 #11457e"></span>
  </div>
  <nav class="nav">
    <span class="active">The enterprise</span><span>Services</span><span>Our projects</span><span>Cooperation partners</span><span>Calls for cooperation</span><span>Contact</span>
  </nav>
  <div class="hero-title">We provide research and<br>innovation programme/projects in<br>wood based industries.</div>
  <a class="btn">Read more</a>
  <div class="arrow-side" style="left:0"><svg width="10" height="16"><path d="M8 1 2 8l6 7" stroke="#fff" fill="none" stroke-width="1.5"/></svg></div>
  <div class="arrow-side" style="right:0"><svg width="10" height="16"><path d="M2 1l6 7-6 7" stroke="#fff" fill="none" stroke-width="1.5"/></svg></div>
  <svg class="diag" style="bottom:0" width="1200" height="80" viewBox="0 0 1200 80" preserveAspectRatio="none">
    <polygon points="0,80 0,72 1200,34 1200,80" fill="#fff"/>
    <polygon points="700,50 1200,18 1200,34 0,72 0,71" fill="#ffc214"/>
  </svg>
</section>

<section class="section welcome">
  <h2>WELCOME TO PRAMENOVA</h2>
  <p class="lead">We start with the administration of EU projects and state aid projects. At present we are working for completed portfolio of clients as supervisors of development and innovative projects. The company 1.Pramenova is registered since 04.04.2008 in the commercial register under ID: 31559027. Since the 06.06.2013 our company is under the registration number 820455017396-21 as "1. Pramenova s.r.o. "has been registered in the Register of European Commission Representatives.</p>
</section>

<section class="section expertise">
  <div class="expertise-copy">
    <h2>AREA OF EXPERTISE</h2>
    <p>Suspendisse gravida ornare erat sed pulvinar. Vestibulum luctus ex in egestas fringilla. Fusce nec leo ac urna pulvinar auctor. Mauris bibendum fringilla velit. Nulla in lorem at massa pellentesque posuere. Nulla tristique posuere molestie. Aliquam erat volutpat. Etiam quis aliquet risus. Duis ornare erat eget magna dapibus, in accumsan quam pharetra. Nam tempus, quam in bibendum.</p>
    <a class="btn">Read more</a>
  </div>
  <div class="expertise-photo" role="img" aria-label="Sawmill hall with stacked timber on production lines"></div>
</section>

<section class="section services">
  <h2>SERVICES PROVIDED BY PRAMENOVA</h2>
  <div class="tiles">
    <div class="tile"><svg width="60" height="56" fill="none" stroke="#21862f" stroke-width="2"><rect x="20" y="2" width="20" height="14"/><path d="M30 16v10M10 26h40M10 26v8M30 26v8M50 26v8"/><rect x="2" y="34" width="16" height="18"/><rect x="22" y="34" width="16" height="18"/><rect x="42" y="34" width="16" height="18"/></svg>Project<br>Coordination</div>
    <div class="tile"><svg width="60" height="56" fill="none" stroke="#21862f" stroke-width="2"><rect x="22" y="2" width="28" height="40" rx="2"/><circle cx="36" cy="20" r="6"/><path d="M6 30h14v22H6zM20 38h12"/></svg>Project Financing<br>&nbsp;</div>
    <div class="tile"><svg width="60" height="56" fill="none" stroke="#21862f" stroke-width="2"><path d="M24 2v24M36 2v24M18 8h24M30 26v14"/><circle cx="30" cy="44" r="6"/><path d="M8 54h44"/></svg>Technology and<br>Foreign Trade Projects</div>
    <div class="tile"><svg width="60" height="56" fill="none" stroke="#21862f" stroke-width="2"><circle cx="30" cy="28" r="24"/><path d="M14 18c8 2 10 8 6 14M40 10c-4 8 2 12 8 12M30 40c4 4 10 2 12 8"/></svg>Framework of<br>international cooperation</div>
    <div class="tile"><svg width="60" height="56" fill="none" stroke="#21862f" stroke-width="2"><path d="M14 52V8h8l18 20v24M6 52h48M22 16v36M30 26v26"/></svg>EU Projects<br>&nbsp;</div>
    <div class="tile"><svg width="60" height="56" fill="none" stroke="#21862f" stroke-width="2"><circle cx="22" cy="22" r="12"/><circle cx="22" cy="22" r="5"/><circle cx="42" cy="40" r="9"/><circle cx="42" cy="40" r="3"/><path d="M22 6v4M22 34v4M6 22h4M34 22h4"/></svg>International<br>Development Projects</div>
    <div class="tile"><svg width="60" height="56" fill="none" stroke="#21862f" stroke-width="2"><rect x="12" y="4" width="36" height="32"/><path d="M24 4v10h12V4M22 28v-8l-3 3M38 28v-8l3 3M8 44h44v6H8z"/></svg>Export Promotion<br>&nbsp;</div>
    <div class="tile more">READ MORE</div>
  </div>
</section>

<section class="section partners">
  <svg class="diag" style="top:0" width="1200" height="78" viewBox="0 0 1200 78" preserveAspectRatio="none">
    <polygon points="0,0 1200,0 1200,4 0,76" fill="#fff"/>
    <polygon points="0,64 1200,0 1200,4 0,76" fill="#ffc214"/>
  </svg>
  <h2>OUR PARTNERS</h2>
  <div class="partner-row">
    <div class="badge" role="img" aria-label="Partner badge" style="width:230px;height:80px"></div>
    <div class="badge" role="img" aria-label="Partner badge" style="width:150px;height:80px"></div>
    <div class="badge" role="img" aria-label="Partner badge" style="width:110px;height:80px"></div>
  </div>
  <svg class="diag" style="bottom:0" width="1200" height="78" viewBox="0 0 1200 78" preserveAspectRatio="none">
    <polygon points="0,78 1200,78 1200,4 0,76" fill="#fff"/>
    <polygon points="0,74 1200,0 1200,14 0,78" fill="#ffc214"/>
  </svg>
</section>

<section class="section conditions">
  <h2>CONDITIONS OF OUR SERVICES</h2>
  <p class="lead">Vestibulum condimentum, risus ut posuere cursus, velit justo accumsan sem, lobortis aliquet metus dui eu libero. Pellentesque a imperdiet dolor, et auctor est. Fusce sollicitudin lorem et luctus volutpat. Proin placerat dapibus gravida. In tristique tristique nulla eget hendrerit. Maecenas vel tortor accumsan quam varius imperdiet vel eget elit. Aenean facilisis tincidunt lectus, id dictum nisi luctus eget. Vivamus efficitur ex condimentum, malesuada eros eget, feugiat nibh. Sed tellus ex, imperdiet eget gravida sit amet.</p>
  <a class="btn">Read more</a>
</section>

<section class="section projects">
  <svg class="diag" style="top:0" width="1200" height="68" viewBox="0 0 1200 68" preserveAspectRatio="none">
    <polygon points="0,0 1200,0 1200,2 0,66" fill="#fff"/>
    <polygon points="0,52 1200,0 1200,3 0,68" fill="#ffc214"/>
  </svg>
  <h2>SUCCESSFUL PROJECTS</h2>
  <svg class="chev" style="left:54px" width="20" height="30"><path d="M16 3 4 15l12 12" stroke="#666" stroke-width="3" fill="none"/></svg>
  <svg class="chev" style="left:1126px" width="20" height="30"><path d="M4 3l12 12L4 27" stroke="#666" stroke-width="3" fill="none"/></svg>
  <div class="cards">
    <div class="card"><div class="card-img" role="img" aria-label="Woodworking machine in a workshop" style="background:linear-gradient(135deg,#8d8a85,#c9c4bb 50%,#5a5750)"></div><p>Etiam mattis augue vehicula odio posuere amet tempus lectus luctus.</p></div>
    <div class="card"><div class="card-img" role="img" aria-label="Video of a timber building project at dusk" style="background:linear-gradient(#1c2a3c,#2a3340 60%,#4a3a2c)"><svg width="36" height="36"><circle cx="18" cy="18" r="17" fill="#fff"/><path d="M14 10v16l12-8z" fill="#222"/></svg></div><p>Quisque aliquet vestibulum pulvinar. Pellen tesque convallis molestie.</p></div>
    <div class="card"><div class="card-img" role="img" aria-label="Newly built residential block" style="background:linear-gradient(#cfd6de,#b89f84 55%,#8b7a6a)"></div><p>Etiam id imperdiet lectus. Vivamus lacus justo, ultrices nec.</p></div>
  </div>
  <svg class="diag" style="bottom:0" width="1200" height="74" viewBox="0 0 1200 74" preserveAspectRatio="none">
    <polygon points="0,74 1200,74 1200,4 0,72" fill="#fff"/>
    <polygon points="0,70 1200,0 1200,14 0,74" fill="#ffc214"/>
  </svg>
</section>

<section class="section team">
  <h2>OUR TEAM</h2>
  <div class="people">
    <div class="person"><div class="person-img" role="img" aria-label="Portrait of Tomas Hrubec" style="background:linear-gradient(#6b705c,#8a7a66)"></div><h3>Tomas Hrubec</h3><span>Geschäftsführer</span></div>
    <div class="person"><div class="person-img" role="img" aria-label="Portrait of Lenka Dvorska" style="background:linear-gradient(#f4f4f4,#d9c2b0)"></div><h3>Mgr. Lenka Dvorska</h3><span>Projekt manager</span></div>
    <div class="person"><div class="person-img" role="img" aria-label="Portrait of Martin Kolar" style="background:linear-gradient(#a9a9a9,#2b2b2b)"></div><h3>Martin Kolar</h3><span>Projektberater</span></div>
    <div class="person"><div class="person-img" role="img" aria-label="Portrait of Klara" style="background:linear-gradient(#7d7d7d,#3aa0c8)"></div><h3>Klara</h3><span>Aliquam dignissim elit nec</span></div>
  </div>
</section>

<section class="section contact">
  <svg class="diag" style="top:0" width="1200" height="78" viewBox="0 0 1200 78" preserveAspectRatio="none">
    <polygon points="0,0 1200,0 1200,2 0,74" fill="#fff"/>
    <polygon points="0,60 1200,0 1200,3 0,76" fill="#ffc214"/>
  </svg>
  <h2>CONTACT INFO</h2>
  <p style="margin-top:8px">1. Pramenova s.r.o, ID 4172, Lindenweg 14, 02799 Musterdorf<br>Phone : 420 555 0147 &nbsp; | &nbsp; Email : info@pramenova-example.eu</p>
  <div class="map" role="img" aria-label="Map showing the office location"></div>
</section>

<footer class="section footer">
  <svg class="diag" style="top:-60px" width="1200" height="62" viewBox="0 0 1200 62" preserveAspectRatio="none">
    <polygon points="0,62 1200,62 1200,0 0,56" fill="#1d1d1d"/>
    <polygon points="0,50 1200,0 1200,4 0,58" fill="#ffc214"/>
  </svg>
  <div class="footer-links">The enterprise<b>|</b>Services<b>|</b>Our projects<b>|</b>Cooperation partners<b>|</b>Calls for cooperation<b>|</b>Contact</div>
  <div class="copy">Copyright © 2019 Pramenova. &nbsp; All rights reserved.</div>
  <div class="social" aria-label="Social links"><span></span><span></span></div>
</footer>

</body>
</html>
```